Clean business card with logo provided

I want a card that will stand out among the masses. I need the color and image to show professionalism and yet have a family appeal showing that I only deal with win/win scenarios. The back of the card will be used to take notes about the individual so I can use that in my database entry. I like modern design but need professionalism in it also. It needs to fit my "clean, safe, and affordable housing" motto. I need to be able to write on the file and update the card details for my employees.

Target Market(s)

Investors looking to make investment income through real estate

Industry/Entity Type

Real Estate

Contact Information for Business Card

Brent Kovalich
blank address, city, st, zip code
480-555-3174
brentkovalich@ridgeworthrentals.example
www.ridgeworthrentals.example

Font styles to use
Sans Serif

Requirements
Must have
• I would like the back of the card to have lines for info. example
• Met/Visited: Date:
• Interets:
Nice to have
• I want the cards color to match the logo background color. Font with details to be san serif and black. I want the card rectangular with square corners. Standard business card size. I would like to see cards designed with both images to see which i prefer more.

```html
<!DOCTYPE html>
<html lang="en">
<head>
<meta charset="utf-8">
<title>Ridgeworth Rentals LLC – Business Card</title>
<link rel="stylesheet" href="https://fonts.googleapis.com/css2?family=Open+Sans:wght@400;600;700&display=swap">
<style>
  :root {
    --backdrop: #2b2d31;
    --card: #ffffff;
    --brand-teal: #1fb3c6;
    --ink: #111111;
    --mark-grey: #d0d0d0;
  }
  * { box-sizing: border-box; margin: 0; padding: 0; }
  html, body {
    width: 1200px; height: 864px; overflow: hidden;
    background: var(--backdrop);
    font-family: "Open Sans", Arial, sans-serif;
  }
  .canvas { position: relative; width: 1200px; height: 864px; }
  .card {
    position: absolute;
    width: 580px; height: 331px;
    background: var(--card);
    overflow: hidden;
  }
  .card--notes { left: 210px; top: 60px; }
  .card--contact { left: 330px; top: 470px; }

  .wordmark { text-align: center; }
  .wordmark__name {
    display: flex; align-items: center; gap: 10px;
    color: var(--brand-teal);
    font-weight: 700; font-size: 30px; letter-spacing: 1px;
    text-transform: uppercase; line-height: 1;
  }
  .wordmark__dot {
    width: 16px; height: 16px; border-radius: 50%;
    background: var(--brand-teal); flex: none;
  }
  .wordmark__tagline {
    margin-top: 6px;
    color: var(--brand-teal);
    font-size: 11px; font-weight: 600;
  }

  .card--notes .wordmark {
    position: absolute; left: 0; right: 0; top: 46px;
    display: flex; flex-direction: column; align-items: center;
  }
  .notes { position: absolute; left: 120px; top: 148px; }
  .notes__row {
    display: flex; align-items: flex-end;
    color: var(--brand-teal); font-weight: 600; font-size: 15px;
    height: 30px;
  }
  .notes__label { white-space: nowrap; margin-right: 6px; }
  .notes__line {
    width: 280px; border-bottom: 2px dotted var(--brand-teal);
    margin-bottom: 4px;
  }

  .card--contact .wordmark {
    position: absolute; left: 40px; top: 34px;
    display: flex; flex-direction: column; align-items: flex-start;
  }
  .contact { position: absolute; left: 40px; top: 120px; color: var(--ink); }
  .contact__name {
    color: var(--brand-teal); font-weight: 700; font-size: 19px;
    margin-bottom: 14px;
  }
  .contact__address { font-size: 14px; line-height: 1.15; margin-bottom: 14px; }
  .contact__list { list-style: none; font-size: 14px; }
  .contact__item { display: flex; align-items: center; gap: 10px; height: 22px; }
  .contact__icon { width: 12px; height: 12px; flex: none; fill: var(--brand-teal); }

  .brand-decoration {
    position: absolute; right: 0; top: 40px;
    width: 260px; height: 260px;
    background: radial-gradient(circle at 60% 50%, var(--mark-grey) 0%, rgba(208,208,208,0.5) 45%, rgba(255,255,255,0) 72%);
  }
</style>
</head>
<body>
<main class="canvas">

  <section class="card card--notes" aria-label="Card back for notes">
    <div class="wordmark">
      <div class="wordmark__name"><span>Ridgeworth Rentals LLC</span><span class="wordmark__dot"></span></div>
      <p class="wordmark__tagline">Providing clean, safe, and affordable housing</p>
    </div>
    <div class="notes">
      <div class="notes__row"><span class="notes__label">Visited Date:</span><span class="notes__line"></span></div>
      <div class="notes__row"><span class="notes__label">Interets:</span><span class="notes__line"></span></div>
      <div class="notes__row"><span class="notes__label">Problems:</span><span class="notes__line"></span></div>
    </div>
  </section>

  <section class="card card--contact" aria-label="Card front with contact details">
    <div class="brand-decoration" role="img" aria-label="Faint large brand mark decoration"></div>
    <div class="wordmark">
      <div class="wordmark__name"><span>Ridgeworth Rentals LLC</span><span class="wordmark__dot"></span></div>
      <p class="wordmark__tagline">Providing clean, safe, and affordable housing</p>
    </div>
    <div class="contact">
      <h1 class="contact__name">Brent Kovalich</h1>
      <p class="contact__address">12345, Address Goes Here<br>Country Name, 123456</p>
      <ul class="contact__list">
        <li class="contact__item">
          <svg class="contact__icon" viewBox="0 0 24 24" aria-hidden="true"><path d="M6.6 10.8a15 15 0 0 0 6.6 6.6l2.2-2.2a1 1 0 0 1 1-.25 11.4 11.4 0 0 0 3.6.57 1 1 0 0 1 1 1V20a1 1 0 0 1-1 1A17 17 0 0 1 3 4a1 1 0 0 1 1-1h3.5a1 1 0 0 1 1 1c0 1.25.2 2.45.57 3.57a1 1 0 0 1-.25 1z"/></svg>
          <span>480-555-3174</span>
        </li>
        <li class="contact__item">
          <svg class="contact__icon" viewBox="0 0 24 24" aria-hidden="true"><path d="M2 5h20v14H2z M2 5l10 8 10-8" /></svg>
          <span>brentkovalich@ridgeworthrentals.example</span>
        </li>
        <li class="contact__item">
          <svg class="contact__icon" viewBox="0 0 24 24" aria-hidden="true"><circle cx="12" cy="12" r="10"/></svg>
          <span>www.ridgeworthrentals.example</span>
        </li>
      </ul>
    </div>
  </section>

</main>
</body>
</html>
```